Stationary Set Rebrand for Brennick

We are a Canadian Distribution and Service Company that was established in 1969. Over the past 5 decades we have expanded our business and have warehouses across Canada. We specialize in adhesive tapes, adhesives, films, safety, warehouse, shipping, janitorial and packaging supplies.

We have updated our logo design and would like a new corporate branding identity that includes a new fresh Stationary Set (Business Cards, Letterhead, Letterhead MS Word, Envelope, Presentation Folders, Email Signatures, Notepad Covers, etc.)

Target Market(s)

Industrial Business Sector

Font styles to use
Sans Serif

Colors
0054AA
0677BA
7BADD7
CADEEF
E8F1F8
0094D4
00A9DD
6FCCEA
C7EBF8
E9F6FB
00AB8E
00BBA5
67D7C9
C6EFE9
E9F9F6
EB3D1F
EC4F4E
F09395
F8D3D4
FCEDEE

Requirements
Should not have
• Colors not too light, darker colours preferred

```html
<!DOCTYPE html>
<html lang="en">
<head>
<meta charset="utf-8">
<title>Brennick Business Card</title>
<link rel="stylesheet" href="https://fonts.googleapis.com/css2?family=Open+Sans:wght@400;700;800&display=swap">
<style>
  :root {
    --bg: #1e1e1e;
    --card: #ffffff;
    --ink: #1c1c1c;
    --text: #3a3a3a;
    --red: #d71920;
    --red-light: #ef3e45;
    --red-dark: #b5121a;
    --band: #1b1b1b;
  }
  html, body {
    margin: 0;
    width: 1200px;
    height: 900px;
    overflow: hidden;
    background: var(--bg);
    font-family: "Open Sans", Arial, sans-serif;
  }
  .card {
    position: absolute;
    left: 250px;
    width: 700px;
    height: 400px;
    overflow: hidden;
  }
  .card-front { top: 40px; background: var(--card); }
  .card-back {
    top: 460px;
    background: linear-gradient(135deg, var(--red-dark) 0%, var(--red) 45%, var(--red-light) 100%);
  }
  .card-art {
    position: absolute;
    inset: 0;
    width: 100%;
    height: 100%;
  }
  .brand {
    position: absolute;
    left: 200px;
    top: 26px;
  }
  .brand-name {
    margin: 0;
    font-size: 54px;
    font-weight: 800;
    line-height: 1;
    color: var(--ink);
  }
  .brand-tagline {
    margin: 4px 0 0;
    font-size: 12px;
    font-weight: 700;
    color: var(--ink);
  }
  .contact {
    position: absolute;
    left: 34px;
    top: 126px;
    color: var(--text);
    font-size: 17px;
    line-height: 1.3;
  }
  .contact-name {
    margin: 0;
    color: var(--red);
    font-weight: 700;
    font-size: 22px;
    letter-spacing: 0.5px;
  }
  .contact-role { margin: 0 0 12px; }
  .contact-address { margin: 0 0 12px; }
  .contact-list { list-style: none; margin: 0; padding: 0; }
  .contact-list li { display: flex; align-items: center; gap: 8px; }
  .contact-icon { width: 15px; height: 15px; flex: none; }
</style>
</head>
<body>
  <main>
    <section class="card card-front">
      <svg class="card-art" viewBox="0 0 700 400">
        <path class="card-band" d="M545 0 H700 V400 H380 C420 310 470 220 545 0 Z" fill="var(--band)"/>
        <path class="card-accent-curve" d="M270 400 C330 378 362 355 392 320" fill="none" stroke="var(--red)" stroke-width="6"/>
        <g role="img" aria-label="Large red maple leaf emblem with white outline">
          <ellipse cx="470" cy="250" rx="155" ry="140" fill="var(--red)" stroke="#ffffff" stroke-width="4"/>
        </g>
      </svg>

      <header class="brand">
        <h1 class="brand-name">Brennick</h1>
        <p class="brand-tagline">Tape and Packaging Specialists</p>
      </header>

      <div class="contact">
        <h2 class="contact-name">DANIEL HARPER</h2>
        <p class="contact-role">Managing Director</p>
        <p class="contact-address">Your Address, City<br>State, Zip 0000</p>
        <ul class="contact-list">
          <li>
            <svg class="contact-icon" viewBox="0 0 20 20" aria-hidden="true"><circle cx="10" cy="10" r="10" fill="var(--red)"/><path d="M5 8 Q10 4 15 8 L13 10 H7 Z M6 11 H14 V15 H6 Z" fill="#fff"/></svg>
            044-123 456 789
          </li>
          <li>
            <svg class="contact-icon" viewBox="0 0 20 20" aria-hidden="true"><circle cx="10" cy="10" r="10" fill="var(--red)"/><rect x="5" y="6.5" width="10" height="7" fill="none" stroke="#fff" stroke-width="1.5"/><path d="M5 6.5 L10 11 L15 6.5" fill="none" stroke="#fff" stroke-width="1.5"/></svg>
            info@webname.com
          </li>
          <li>
            <svg class="contact-icon" viewBox="0 0 20 20" aria-hidden="true"><circle cx="10" cy="10" r="10" fill="var(--red)"/><circle cx="10" cy="10" r="5" fill="none" stroke="#fff" stroke-width="1.5"/><path d="M5 10 H15 M10 5 V15" stroke="#fff" stroke-width="1.2"/></svg>
            www.websitename.com
          </li>
        </ul>
      </div>
    </section>

    <section class="card card-back" role="img" aria-label="Card back: repeating pattern of maple leaves in light and dark red tones, with one white maple leaf near the lower right"></section>
  </main>
</body>
</html>
```